you will use Ai to Copy the website Brivanta.com to come up with the basic frame work and it will give you the understanding of how I would like Kelbrava.com to be like. Kelbrava.com is a peer to peer rv rental site very similar to both of the other rv rental sites the difference is that are commission based 20% and above per rental and we will be one flat monthly rate and they keep all the earnings. Below is photo that will help you with the color scheme and the look and feel of the design

1 page

```html
<!DOCTYPE html>
<html lang="en">
<head>
<meta charset="utf-8">
<title>Kelbrava.com — Browse RVs and How it works</title>
<link href="https://fonts.googleapis.com/css2?family=Fraunces:opsz,wght@9..144,600;9..144,700&family=Outfit:wght@400;500;600;700&family=JetBrains+Mono:wght@500&display=swap" rel="stylesheet">
<style>
:root{
  --navy:#0e1a33;
  --navy-2:#15223f;
  --navy-line:#24324f;
  --green:#8cc63f;
  --green-dark:#6fa52a;
  --cream:#f7f5ef;
  --canvas:#f1eee6;
  --card:#ffffff;
  --ink:#111a2c;
  --muted:#6b7282;
  --line:#e4e1d8;
  --white:#ffffff;
  --footer-text:#aab3c5;
  --serif:"Fraunces",Georgia,serif;
  --sans:"Outfit",Helvetica,Arial,sans-serif;
  --mono:"JetBrains Mono",Menlo,monospace;
}
*{box-sizing:border-box;margin:0;padding:0}
html,body{width:1200px;height:781px;overflow:hidden;background:var(--canvas)}
body{font-family:var(--sans);color:var(--ink)}
.stage{position:absolute;left:0;top:0;width:2380px;height:1550px;transform:scale(.504202);transform-origin:0 0;background:var(--canvas)}
.abs{position:absolute}
.section-label{position:absolute;top:42px;font-family:var(--sans);font-size:29px;font-weight:400;color:#5c6170;letter-spacing:.2px}
.page{position:absolute;top:90px;width:866px;background:var(--cream);box-shadow:0 30px 60px rgba(20,25,40,.12);overflow:hidden}
.page-browse{left:292px;height:1253px}
.page-how{left:1254px;height:1361px}

/* header */
.site-header{position:absolute;left:0;top:0;width:100%;background:var(--navy)}
.brand{position:absolute;left:49px;top:10px;font-family:var(--sans);font-weight:700;font-size:25px;color:var(--white);letter-spacing:-.3px}
.main-nav{position:absolute;left:331px;top:19px;display:flex;gap:20px;font-size:8.5px;color:#dfe4ee}
.login{position:absolute;left:697px;top:19px;font-size:8.5px;color:#dfe4ee}
.btn-list{position:absolute;left:729px;top:12px;width:89px;height:26px;border-radius:4px;background:var(--green);color:var(--navy);font-size:8.5px;font-weight:600;display:flex;align-items:center;justify-content:center;gap:4px}
.search-row{position:absolute;left:49px;right:48px;top:82px;display:flex;justify-content:space-between;font-size:8px}
.search-row .where{color:#cfd5e1;display:flex;gap:5px;align-items:center}
.search-row .edit{color:var(--green);font-weight:600}

/* filters */
.filters{position:absolute;left:49px;top:133px;width:166px}
.filters h3{font-family:var(--serif);font-size:12px;font-weight:600}
.clear-all{position:absolute;right:0;top:2px;font-size:8px;color:var(--green)}
.f-label{position:absolute;left:0;font-size:8px;font-weight:600}
.type-btn{position:absolute;left:0;width:166px;height:23px;border:1px solid var(--line);border-radius:3px;background:var(--white);font-size:8px;padding-left:8px;display:flex;align-items:center}
.type-btn.active{background:var(--green);border-color:var(--green);font-weight:500}
.slider{position:absolute;left:0;top:286px;width:166px;height:4px;border-radius:2px;background:var(--green)}
.slider::after{content:"";position:absolute;right:-2px;top:-3px;width:10px;height:10px;border-radius:50%;background:var(--green);border:1px solid #fff}
.range-lbl{position:absolute;top:301px;font-size:7px;color:var(--muted)}
.chip{position:absolute;height:21px;border:1px solid var(--line);border-radius:4px;background:var(--white);font-size:8px;display:flex;align-items:center;justify-content:center}
.chip.active{background:var(--green);border-color:var(--green)}
.option{position:absolute;left:0;display:flex;align-items:center;gap:7px;font-size:8px}
.option i{width:12px;height:12px;border:1px solid #9aa1ae;border-radius:2px;background:#fff;display:block}

/* results */
.results-head{position:absolute;left:236px;top:131px;width:581px}
.results-head h1{font-family:var(--serif);font-size:20px;font-weight:600;line-height:1}
.results-head p{font-size:7.5px;color:var(--muted);margin-top:6px}
.sort{position:absolute;right:0;top:7px;display:flex;align-items:center;gap:6px;font-size:8px;color:var(--muted)}
.sort .select{width:96px;height:23px;border:1px solid var(--line);border-radius:3px;background:#fff;color:var(--ink);display:flex;align-items:center;justify-content:space-between;padding:0 6px 0 9px}

.card{position:absolute;width:180px;height:272px;background:var(--card);border:1px solid var(--line);border-radius:5px;overflow:hidden}
.photo{height:134px;position:relative}
.tags{position:absolute;left:8px;top:9px;display:flex;gap:4px}
.tag{height:14px;padding:0 6px;border-radius:7px;font-size:6.5px;font-weight:600;display:flex;align-items:center;gap:3px}
.tag-ib{background:var(--green);color:var(--navy)}
.tag-del{background:var(--navy);color:#fff}
.fav{position:absolute;right:9px;top:9px;width:20px;height:20px;border-radius:50%;background:rgba(255,255,255,.92);display:flex;align-items:center;justify-content:center}
.card-body{padding:13px 13px 0}
.meta-row{display:flex;justify-content:space-between;align-items:center;height:12px}
.rv-class{font-size:6.5px;font-weight:600;color:var(--green);letter-spacing:.4px;text-transform:uppercase}
.rating{font-size:7.5px;display:flex;gap:2px;align-items:center}
.rating span{color:var(--muted)}
.card h4{font-family:var(--serif);font-size:11.5px;font-weight:600;margin-top:6px;line-height:16px}
.info{font-size:7.5px;color:#4d5464;display:flex;align-items:center;gap:4px;height:15px}
.info + .info{border-bottom:1px solid var(--line);padding-bottom:2px;height:17px}
.price-row{display:flex;align-items:baseline;gap:3px;margin-top:9px}
.price{font-size:17px;font-weight:500}
.per{font-size:7.5px;color:var(--muted)}
.foot-row{display:flex;justify-content:space-between;align-items:center;margin-top:4px}
.foot-row small{font-size:6px;color:var(--muted)}
.foot-row b{font-size:7.5px;font-weight:600}

/* footer */
.site-footer{position:absolute;left:0;width:100%;height:431px;background:radial-gradient(circle at 62% 58%,#16254a 0%,var(--navy) 55%);color:var(--white)}
.news-title{position:absolute;left:49px;top:50px;font-family:var(--serif);font-size:31px;line-height:31px;font-weight:600}
.news-text{position:absolute;left:49px;top:124px;width:270px;font-size:9px;line-height:15px;color:#d6dbe6}
.email-lbl{position:absolute;left:448px;top:68px;font-size:8px}
.email-input{position:absolute;left:448px;top:84px;width:269px;height:30px;border:1px solid #34425f;border-radius:3px;background:#1a2745;font-size:8px;color:#8d97ab;display:flex;align-items:center;gap:6px;padding-left:11px}
.btn-sub{position:absolute;left:725px;top:84px;width:92px;height:30px;border-radius:3px;background:var(--green);color:var(--navy);font-size:9.5px;font-weight:600;display:flex;align-items:center;justify-content:center;gap:5px}
.consent{position:absolute;left:448px;top:124px;font-size:6.5px;color:#b8c0d0;display:flex;gap:5px;align-items:center}
.consent i{width:7px;height:7px;background:#fff;display:block;border-radius:1px}
.consent u{color:#fff}
.f-divider{position:absolute;left:0;width:100%;height:1px;background:var(--navy-line)}
.f-brand{position:absolute;left:49px;top:223px;font-weight:700;font-size:24px}
.f-tag{position:absolute;left:49px;top:259px;font-size:6.5px;letter-spacing:2px;color:var(--green);font-weight:600}
.f-desc{position:absolute;left:49px;top:282px;width:200px;font-size:7.5px;line-height:15px;color:var(--footer-text)}
.f-trust{position:absolute;left:49px;top:324px;font-size:7.5px;color:#d5dae4;display:flex;gap:6px;align-items:center}
.f-col{position:absolute;top:228px}
.f-col h5{font-size:7.5px;font-weight:600;letter-spacing:.6px;margin-bottom:12px}
.f-col li{list-style:none;font-size:7.5px;color:var(--footer-text);height:22px}
.f-copy{position:absolute;left:49px;top:405px;font-size:7.5px;color:var(--footer-text)}
.f-legal{position:absolute;right:48px;top:405px;font-size:7.5px;color:var(--footer-text);display:flex;gap:14px}

/* how it works */
.hero{height:257px}
.eyebrow{position:absolute;left:171px;top:106px;font-size:8px;font-weight:600;letter-spacing:2px;color:var(--green)}
.hero h1{position:absolute;left:171px;top:122px;font-family:var(--serif);font-size:31px;font-weight:600;color:#fff;line-height:1.1}
.hero p{position:absolute;left:171px;top:169px;width:440px;font-size:10px;line-height:19px;color:#dfe4ee}
.step{position:absolute;top:309px;width:160px;height:213px;background:#fff;border:1px solid var(--line);border-radius:5px;padding:15px}
.step-top{display:flex;align-items:center;gap:9px}
.step-icon{width:30px;height:30px;border-radius:4px;background:#e9f3da;display:flex;align-items:center;justify-content:center}
.step-num{font-family:var(--mono);font-size:17px;color:#aeb3bd}
.step h4{font-family:var(--serif);font-size:12.5px;font-weight:600;margin-top:13px;line-height:18px}
.step p{font-size:8.5px;line-height:16.7px;color:#4d5464;margin-top:7px}
.protect{position:absolute;left:171px;top:553px;width:522px;height:193px;background:var(--navy);border-radius:8px}
.protect h3{position:absolute;left:26px;top:26px;font-family:var(--serif);font-size:14.5px;font-weight:600;color:#fff}
.p-card{position:absolute;top:62px;width:147px;height:105px;border:1px solid var(--navy-line);background:var(--navy-2);border-radius:4px;padding:13px}
.p-card h5{font-size:8.5px;font-weight:600;color:#fff;margin-top:6px}
.p-card p{font-size:7px;line-height:13px;color:#b8c0d0;margin-top:3px}
.p-card b{display:block;font-size:7px;color:var(--green);font-weight:600;margin-top:6px}
.note{position:absolute;left:171px;top:767px;width:522px;height:40px;background:#efece4;border:1px solid var(--line);border-radius:4px;font-size:7px;color:#4d5464;display:flex;align-items:center;padding-left:13px}
.note strong{color:var(--ink);font-weight:600;margin-right:3px}
.cta{position:absolute;top:833px;height:34px;border-radius:4px;font-size:9px;font-weight:600;display:flex;align-items:center;justify-content:center;gap:5px}
.cta-primary{left:171px;width:100px;background:var(--green);color:var(--navy)}
.cta-ghost{left:282px;width:104px;background:#fff;border:1px solid var(--line)}
</style>
</head>
<body>
<div class="stage">

  <div class="section-label" style="left:292px">02 Browse RV Page</div>
  <div class="section-label" style="left:1254px">03 How it works Page</div>

  <!-- Browse page -->
  <section class="page page-browse">
    <header class="site-header" style="height:115px">
      <div class="brand">Kelbrava.com</div>
      <nav class="main-nav"><span>Browse RVs</span><span>How it works</span><span>For owners</span><span>Help</span></nav>
      <span class="login">Log in</span>
      <span class="btn-list"><svg width="8" height="7" viewBox="0 0 8 7"><path d="M0 1h1M2 1h6M0 3.5h1M2 3.5h6M0 6h1M2 6h6" stroke="#0e1a33" stroke-width="1"/></svg>List your RV</span>
      <div class="search-row">
        <span class="where"><svg width="8" height="9" viewBox="0 0 8 9"><path d="M4 8.5S7 5.6 7 3.5a3 3 0 0 0-6 0C1 5.6 4 8.5 4 8.5z" fill="none" stroke="#cfd5e1" stroke-width=".9"/><circle cx="4" cy="3.5" r="1" fill="#cfd5e1"/></svg>Anywhere</span>
        <span class="edit">Edit search</span>
      </div>
    </header>

    <aside class="filters">
      <h3>Filters</h3><span class="clear-all">Clear all</span>
      <span class="f-label" style="top:34px">RV type</span>
      <div class="type-btn active" style="top:53px">Any type</div>
      <div class="type-btn" style="top:81px">Class A</div>
      <div class="type-btn" style="top:109px">Class B</div>
      <div class="type-btn" style="top:137px">Class C</div>
      <div class="type-btn" style="top:165px">Travel Trailer</div>
      <div class="type-btn" style="top:193px">Fifth Wheel</div>
      <div class="type-btn" style="top:221px">Aerliner</div>
      <span class="f-label" style="top:266px">Max price per night</span>
      <div class="slider"></div>
      <span class="range-lbl" style="left:0">$50</span><span class="range-lbl" style="right:0">$250+</span>
      <span class="f-label" style="top:331px">Sleeps</span>
      <span class="chip" style="left:0;top:349px;width:25px">2+</span>
      <span class="chip" style="left:32px;top:349px;width:25px">4+</span>
      <span class="chip" style="left:64px;top:349px;width:25px">6+</span>
      <span class="f-label" style="top:390px">Minimum rating</span>
      <span class="chip active" style="left:0;top:408px;width:32px">Any</span>
      <span class="chip" style="left:38px;top:408px;width:35px">4★+</span>
      <span class="chip" style="left:79px;top:408px;width:41px">4.5★+</span>
      <span class="chip" style="left:127px;top:408px;width:34px">5★+</span>
      <span class="f-label" style="top:449px">Options</span>
      <span class="option" style="top:467px"><i></i>Instant Book</span>
      <span class="option" style="top:485px"><i></i>Delivery available</span>
      <span class="option" style="top:503px"><i></i>Pet-friendly</span>
    </aside>

    <div class="results-head">
      <h1>6 RVs available</h1>
      <p>Showing all available RVs</p>
      <div class="sort">Sort <span class="select">Recommended <svg width="6" height="4" viewBox="0 0 6 4"><path d="M.5.5 3 3 5.5.5" fill="none" stroke="#111a2c" stroke-width=".8"/></svg></span></div>
    </div>

    <article class="card" style="left:236px;top:185px">
      <div class="photo" role="img" aria-label="Class A motorhome on a desert cliff at sunset" style="background:linear-gradient(180deg,#3d4f6e 0%,#c9763e 45%,#8a3f22 75%,#4b2a1e 100%)">
        <div class="tags"><span class="tag tag-ib">⚡ Instant Book</span><span class="tag tag-del">▭ Delivery</span></div>
        <span class="fav"><svg width="9" height="8" viewBox="0 0 9 8"><path d="M4.5 7.5S.5 5 .5 2.5A2 2 0 0 1 4.5 2a2 2 0 0 1 4 .5C8.5 5 4.5 7.5 4.5 7.5z" fill="none" stroke="#111a2c" stroke-width=".8"/></svg></span>
      </div>
      <div class="card-body">
        <div class="meta-row"><span class="rv-class">Class A</span><span class="rating"><em style="color:#e8a13a;font-style:normal">★</em>4.9 <span>(127)</span></span></div>
        <h4>Wanderlust Class A Diesel</h4>
        <div class="info">⌖ Sedona, Arizona</div>
        <div class="info">⚇ Sleeps 6 &nbsp;✿ Pet-friendly</div>
        <div class="price-row"><span class="price">$185</span><span class="per">/night</span></div>
        <div class="foot-row"><small>Transparent pricing</small><b>View details →</b></div>
      </div>
    </article>

    <article class="card" style="left:437px;top:185px">
      <div class="photo" role="img" aria-label="Class B camper van beside a mountain lake" style="background:linear-gradient(180deg,#b9c3c6 0%,#6f8275 40%,#3e5446 70%,#8c8a72 100%)">
        <div class="tags"><span class="tag tag-ib">⚡ Instant Book</span><span class="tag tag-del">▭ Delivery</span></div>
        <span class="fav"><svg width="9" height="8" viewBox="0 0 9 8"><path d="M4.5 7.5S.5 5 .5 2.5A2 2 0 0 1 4.5 2a2 2 0 0 1 4 .5C8.5 5 4.5 7.5 4.5 7.5z" fill="none" stroke="#111a2c" stroke-width=".8"/></svg></span>
      </div>
      <div class="card-body">
        <div class="meta-row"><span class="rv-class">Class B</span><span class="rating"><em style="color:#e8a13a;font-style:normal">★</em>4.8 <span>(89)</span></span></div>
        <h4>Nomad Van — Class B</h4>
        <div class="info">⌖ Lake Tahoe, California</div>
        <div class="info">⚇ Sleeps 2 &nbsp;✿ Pet-friendly</div>
        <div class="price-row"><span class="price">$145</span><span class="per">/night</span></div>
        <div class="foot-row"><small>Transparent pricing</small><b>View details →</b></div>
      </div>
    </article>

    <article class="card" style="left:638px;top:185px">
      <div class="photo" role="img" aria-label="Travel trailer camped in a sunlit pine forest" style="background:linear-gradient(180deg,#d8b46a 0%,#6f7a3c 35%,#2f3d25 70%,#4a4030 100%)">
        <div class="tags"><span class="tag tag-del">▭ Delivery</span></div>
        <span class="fav"><svg width="9" height="8" viewBox="0 0 9 8"><path d="M4.5 7.5S.5 5 .5 2.5A2 2 0 0 1 4.5 2a2 2 0 0 1 4 .5C8.5 5 4.5 7.5 4.5 7.5z" fill="none" stroke="#111a2c" stroke-width=".8"/></svg></span>
      </div>
      <div class="card-body">
        <div class="meta-row"><span class="rv-class">Travel Trailer</span><span class="rating"><em style="color:#e8a13a;font-style:normal">★</em>4.7 <span>(64)</span></span></div>
        <h4>Pinecrest Travel Trailer</h4>
        <div class="info">⌖ Bend, Oregon</div>
        <div class="info">⚇ Sleeps 4 &nbsp;✿ Pet-friendly</div>
        <div class="price-row"><span class="price">$95</span><span class="per">/night</span></div>
        <div class="foot-row"><small>Transparent pricing</small><b>View details →</b></div>
      </div>
    </article>

    <article class="card" style="left:236px;top:478px">
      <div class="photo" role="img" aria-label="Fifth wheel and pickup truck among red canyon rocks" style="background:linear-gradient(180deg,#e3b27a 0%,#b8613a 40%,#8a3b25 70%,#5a2d20 100%)">
        <div class="tags"><span class="tag tag-ib">⚡ Instant Book</span><span class="tag tag-del">▭ Delivery</span></div>
        <span class="fav"><svg width="9" height="8" viewBox="0 0 9 8"><path d="M4.5 7.5S.5 5 .5 2.5A2 2 0 0 1 4.5 2a2 2 0 0 1 4 .5C8.5 5 4.5 7.5 4.5 7.5z" fill="none" stroke="#111a2c" stroke-width=".8"/></svg></span>
      </div>
      <div class="card-body">
        <div class="meta-row"><span class="rv-class">Fifth Wheel</span><span class="rating"><em style="color:#e8a13a;font-style:normal">★</em>4.9 <span>(102)</span></span></div>
        <h4>Desert Rose Fifth Wheel</h4>
        <div class="info">⌖ Moab, Utah</div>
        <div class="info">⚇ Sleeps 5</div>
        <div class="price-row"><span class="price">$130</span><span class="per">/night</span></div>
        <div class="foot-row"><small>Transparent pricing</small><b>View details →</b></div>
      </div>
    </article>

    <article class="card" style="left:437px;top:478px">
      <div class="photo" role="img" aria-label="Class C motorhome in an alpine wildflower meadow" style="background:linear-gradient(180deg,#c5d0d8 0%,#8ea0a8 30%,#4f6b48 65%,#6a7a3e 100%)">
        <span class="fav"><svg width="9" height="8" viewBox="0 0 9 8"><path d="M4.5 7.5S.5 5 .5 2.5A2 2 0 0 1 4.5 2a2 2 0 0 1 4 .5C8.5 5 4.5 7.5 4.5 7.5z" fill="none" stroke="#111a2c" stroke-width=".8"/></svg></span>
      </div>
      <div class="card-body">
        <div class="meta-row"><span class="rv-class">Class C</span><span class="rating"><em style="color:#e8a13a;font-style:normal">★</em>4.6 <span>(51)</span></span></div>
        <h4>Summit Class C</h4>
        <div class="info">⌖ Denver, Colorado</div>
        <div class="info">⚇ Sleeps 4 &nbsp;✿ Pet-friendly</div>
        <div class="price-row"><span class="price">$115</span><span class="per">/night</span></div>
        <div class="foot-row"><small>Transparent pricing</small><b>View details →</b></div>
      </div>
    </article>

    <article class="card" style="left:638px;top:478px">
      <div class="photo" role="img" aria-label="Silver trailer on a coastal bluff at sunset" style="background:linear-gradient(180deg,#4a5a78 0%,#c48a5a 40%,#5b6a6c 70%,#3a4532 100%)">
        <div class="tags"><span class="tag tag-ib">⚡ Instant Book</span><span class="tag tag-del">▭ Delivery</span></div>
        <span class="fav"><svg width="9" height="8" viewBox="0 0 9 8"><path d="M4.5 7.5S.5 5 .5 2.5A2 2 0 0 1 4.5 2a2 2 0 0 1 4 .5C8.5 5 4.5 7.5 4.5 7.5z" fill="none" stroke="#111a2c" stroke-width=".8"/></svg></span>
      </div>
      <div class="card-body">
        <div class="meta-row"><span class="rv-class">Aerliner</span><span class="rating"><em style="color:#e8a13a;font-style:normal">★</em>5 <span>(78)</span></span></div>
        <h4>Silver Stream Aerliner</h4>
        <div class="info">⌖ Big Sur, California</div>
        <div class="info">⚇ Sleeps 2</div>
        <div class="price-row"><span class="price">$160</span><span class="per">/night</span></div>
        <div class="foot-row"><small>Transparent pricing</small><b>View details →</b></div>
      </div>
    </article>

    <footer class="site-footer" style="top:822px">
      <h2 class="news-title">Your next adventure<br>starts with one flat fee</h2>
      <p class="news-text">Get renter deals and owner tips from Kelbrava. For both renters and owners.</p>
      <span class="email-lbl">Email address</span>
      <div class="email-input">✉ you@email.com</div>
      <span class="btn-sub">Subscribe →</span>
      <span class="consent"><i></i>I agree to receive marketing emails and accept the <u>Privacy Policy</u>. Unsubscribe anytime.</span>
      <div class="f-divider" style="top:189px"></div>
      <div class="f-brand">Kelbrava.com</div>
      <div class="f-tag">LIST IT · RENT IT · BANK IT</div>
      <p class="f-desc">The peer-to-peer RV marketplace built on a flat fee. No commission, ever.</p>
      <span class="f-trust">⛉ Trust &amp; Safety</span>
      <div class="f-col" style="left:313px"><h5>RENT</h5><ul><li>Browse RVs</li><li>How it works</li><li>Instant Book</li><li>Insurance</li><li>Roadside Assistance</li></ul></div>
      <div class="f-col" style="left:446px"><h5>LIST</h5><ul><li>List your RV</li><li>Flat-fee pricing</li><li>Owner resources</li><li>Profit calculator</li></ul></div>
      <div class="f-col" style="left:579px"><h5>COMPANY</h5><ul><li>About</li><li>Contact</li><li>Help Center</li><li>Trust &amp; Safety</li></ul></div>
      <div class="f-col" style="left:711px"><h5>LEGAL</h5><ul><li>Terms</li><li>Privacy</li><li>Cookies</li><li>Cancellation Policy</li></ul></div>
      <div class="f-divider" style="top:386px"></div>
      <span class="f-copy">© 2026 Kelbrava.com — Flat fee. Full freedom.</span>
      <span class="f-legal"><span>Terms</span><span>Privacy</span><span>Cookies</span></span>
    </footer>
  </section>

  <!-- How it works page -->
  <section class="page page-how">
    <header class="site-header hero">
      <div class="brand">Kelbrava.com</div>
      <nav class="main-nav"><span>Browse RVs</span><span>How it works</span><span>For owners</span><span>Help</span></nav>
      <span class="login">Log in</span>
      <span class="btn-list"><svg width="8" height="7" viewBox="0 0 8 7"><path d="M0 1h1M2 1h6M0 3.5h1M2 3.5h6M0 6h1M2 6h6" stroke="#0e1a33" stroke-width="1"/></svg>List your RV</span>
      <span class="eyebrow">HOW IT WORKS</span>
      <h1>Renting an RV, made simple</h1>
      <p>From first search to final return, here's how renting on Kelbrava works — and how the flat-fee model keeps it honest for everyone.</p>
    </header>

    <div class="step" style="left:171px">
      <div class="step-top"><span class="step-icon"><svg width="13" height="11" viewBox="0 0 13 11"><path d="M.5 1.5 4.5.5l4 1 4-1v9l-4 1-4-1-4 1z M4.5.5v9M8.5 1.5v9" fill="none" stroke="#8cc63f" stroke-width="1"/></svg></span><span class="step-num">01</span></div>
      <h4>Find your RV</h4>
      <p>Search by location, dates, and rig type. Filter for instant book, delivery, and pet-friendly options to find the perfect rig.</p>
    </div>
    <div class="step" style="left:352px">
      <div class="step-top"><span class="step-icon"><svg width="13" height="13" viewBox="0 0 13 13"><circle cx="6.5" cy="6.5" r="5.5" fill="none" stroke="#8cc63f"/><circle cx="6.5" cy="5.5" r="1.6" fill="none" stroke="#8cc63f"/><path d="M6.5 7v2.5" stroke="#8cc63f"/></svg></span><span class="step-num">02</span></div>
      <h4>Book securely</h4>
      <p>Message the owner, confirm your dates, and book with secure payments. Owner and renter identity verification helps protect every trip.</p>
    </div>
    <div class="step" style="left:534px">
      <div class="step-top"><span class="step-icon"><svg width="15" height="11" viewBox="0 0 15 11"><rect x=".5" y=".5" width="10" height="7" fill="none" stroke="#8cc63f"/><path d="M10.5 3h3l1 2.5v2h-4" fill="none" stroke="#8cc63f"/><circle cx="3.5" cy="9" r="1.3" fill="none" stroke="#8cc63f"/><circle cx="11.5" cy="9" r="1.3" fill="none" stroke="#8cc63f"/></svg></span><span class="step-num">03</span></div>
      <h4>Pick up or get<br>delivery</h4>
      <p>Pick up the keys and get a walkthrough from the owner, or have the RV delivered to your campsite. Return it when your trip is done.</p>
    </div>

    <div class="protect">
      <h3>Protected every mile of the journey</h3>
      <div class="p-card" style="left:26px"><svg width="10" height="11" viewBox="0 0 10 11"><path d="M5 .5 9.5 2v3.5C9.5 8 7.5 9.8 5 10.5 2.5 9.8.5 8 .5 5.5V2z M3 5.5l1.5 1.5L7 4.5" fill="none" stroke="#8cc63f"/></svg><h5>Insurance</h5><p>Insurance protection options are available for every trip.</p><b>Learn more →</b></div>
      <div class="p-card" style="left:188px"><svg width="11" height="11" viewBox="0 0 11 11"><circle cx="5.5" cy="5.5" r="5" fill="none" stroke="#8cc63f"/><circle cx="5.5" cy="5.5" r="2" fill="none" stroke="#8cc63f"/></svg><h5>Roadside assistance</h5><p>24/7 roadside help for covered trips.</p><b>Learn more →</b></div>
      <div class="p-card" style="left:350px"><svg width="9" height="11" viewBox="0 0 9 11"><path d="M.5.5h5l3 3v7H.5z M2.5 6h4M2.5 8h4" fill="none" stroke="#8cc63f"/></svg><h5>Cancellation policy</h5><p>Clear terms if your plans change.</p><b>Learn more →</b></div>
    </div>

    <div class="note"><strong>Internal placeholder —</strong> Confirm exact insurance coverage, roadside response process, and verification details before launch.</div>

    <span class="cta cta-primary">Browse RVs →</span>
    <span class="cta cta-ghost">List your RV →</span>

    <footer class="site-footer" style="top:929px">
      <h2 class="news-title">Your next adventure<br>starts with one flat fee</h2>
      <p class="news-text">Get renter deals and owner tips from Kelbrava. For both renters and owners.</p>
      <span class="email-lbl">Email address</span>
      <div class="email-input">✉ you@email.com</div>
      <span class="btn-sub">Subscribe →</span>
      <span class="consent"><i></i>I agree to receive marketing emails and accept the <u>Privacy Policy</u>. Unsubscribe anytime.</span>
      <div class="f-divider" style="top:189px"></div>
      <div class="f-brand">Kelbrava.com</div>
      <div class="f-tag">LIST IT · RENT IT · BANK IT</div>
      <p class="f-desc">The peer-to-peer RV marketplace built on a flat fee. No commission, ever.</p>
      <span class="f-trust">⛉ Trust &amp; Safety</span>
      <div class="f-col" style="left:313px"><h5>RENT</h5><ul><li>Browse RVs</li><li>How it works</li><li>Instant Book</li><li>Insurance</li><li>Roadside Assistance</li></ul></div>
      <div class="f-col" style="left:446px"><h5>LIST</h5><ul><li>List your RV</li><li>Flat-fee pricing</li><li>Owner resources</li><li>Profit calculator</li></ul></div>
      <div class="f-col" style="left:579px"><h5>COMPANY</h5><ul><li>About</li><li>Contact</li><li>Help Center</li><li>Trust &amp; Safety</li></ul></div>
      <div class="f-col" style="left:711px"><h5>LEGAL</h5><ul><li>Terms</li><li>Privacy</li><li>Cookies</li><li>Cancellation Policy</li></ul></div>
      <div class="f-divider" style="top:386px"></div>
      <span class="f-copy">© 2026 Kelbrava.com — Flat fee. Full freedom.</span>
      <span class="f-legal"><span>Terms</span><span>Privacy</span><span>Cookies</span></span>
    </footer>
  </section>

</div>
</body>
</html>
```